Environmental Consultancey needs Web Design

A consultancey firm based in Papua New Guinea specialising servicing a client market primarily in Melanesia, the wider Pacific Region and South East Asia. The firm provides services to community development and resource extraction activites that incorporate sustainable livelihoods for local customary land owners with environmentally responsibile practices and a focus on maintaining biodiversity and ecosystem services. We aim to encompass Culture, Custom and Science in our approach. Our website preferentially will convey a relaxed Pacific Island feel in its colours and design rather than a sterile corporate feel. See attached logo that will need to be visible on page or which may provide basis for ideas for the page.

Target Market(s)

Our target market is primarily the oil, gas and mining industry, secondarily international donor and aid programs followed by government projects and not for profit programs. Services include:
1. Biodiversity and Conservation - Fauna and Flora survey, assessment, management, monitoring & research, protected areas & endangered & threatend species.
2. Social & Community - impact, stakeholder engagement, census and survey, land and community affairs, capacity building empowerment.
3. Environmental Management - sustainable use, enterprise development & management, biodiversity offsets.

Industry/Entity Type

Community

Requirements
Must have
• Multiple pages, Logo somewhere on home page. Space for a couple of photos that as yet ive not decieded upon.
Nice to have
• Perhaps incorporate shapes, texture and colours that convey a feel of the attached photo of a blue bird of paradise. The blue fine overlapping and interlocking feather patterns are appealing perhaps as a background and the other colours used in boarders ? Abstract is fine as would be symbolic images or tribal ambience. The company is all about blending humanity in all its forms with the environment.

```html
<!DOCTYPE html>
<html lang="en">
<head>
<meta charset="utf-8">
<title>Lagoon Habitat</title>
<link href="https://fonts.googleapis.com/css2?family=Source+Sans+3:ital,wght@0,400;0,600;1,400&display=swap" rel="stylesheet">
<style>
:root{
  --sky-top:#4fa7dc;
  --sky-mid:#a9d8f2;
  --sky-low:#d8eef9;
  --nav-green:#3daa2f;
  --nav-green-dark:#2e9324;
  --nav-active:#5cc24a;
  --heading-green:#1f8a3a;
  --heading-teal:#1e8aa8;
  --body-text:#555c60;
  --link-blue:#1b6f9a;
  --panel-white:#ffffff;
  --blog-bg:#f3f4f5;
  --footer-teal:#2bb3d6;
  --footer-deep:#1a98c2;
  --bar-light:#8fd8ee;
  --bar-text:#1f7ea3;
  --thumb-border:#d7d7d7;
}
*{box-sizing:border-box;margin:0;padding:0}
html,body{width:822px;height:1200px;overflow:hidden}
body{
  position:relative;
  font-family:"Source Sans 3",Arial,sans-serif;
  background:linear-gradient(180deg,var(--sky-top) 0%,var(--sky-mid) 14%,var(--sky-low) 35%,#e9f6fb 78%);
  color:var(--body-text);
}
.abs{position:absolute}
.brand{left:30px;top:28px;display:flex;align-items:center;gap:10px}
.brand-mark{width:26px;height:26px;border-radius:50%;background:var(--nav-green)}
.brand-name{font-size:22px;font-weight:600;color:#244d6b}
.search{left:603px;top:71px;width:183px;height:24px;border-radius:12px;background:#fff;box-shadow:0 1px 3px rgba(0,0,0,.2);font-size:10px;color:#6e8a9a;padding:6px 12px}
.search svg{position:absolute;right:8px;top:4px}
.nav{left:18px;top:126px;width:779px;height:44px;background:linear-gradient(180deg,var(--nav-green),var(--nav-green-dark));border-radius:4px 4px 0 0;display:flex;align-items:center}
.nav a{color:#fff;text-decoration:none;font-size:14px;height:44px;line-height:44px;flex:1;text-align:center;border-left:1px solid rgba(255,255,255,.25)}
.nav a:first-child{border-left:none}
.nav a.active span{background:var(--nav-active);padding:5px 16px;border-radius:3px}
.hero{left:18px;top:170px;width:779px;height:247px}
.hero-caption{left:18px;top:277px;width:337px;height:51px;background:rgba(255,255,255,.55);font-size:18px;color:#1d3a40;padding:13px 10px}
.hero-dots{left:741px;top:401px;display:flex;gap:3px}
.hero-dots i{width:8px;height:8px;background:#fff;display:block}
.content{left:18px;top:417px;width:779px;height:543px;background:var(--panel-white)}
h2{font-weight:400;font-size:19px}
.welcome-title{left:35px;top:438px;color:var(--heading-green)}
.welcome-text{left:35px;top:465px;width:478px;font-size:8.6px;line-height:16px}
.welcome-text p+p{margin-top:4px}
.read-more{left:35px;top:605px;font-size:11px;color:#333}
.projects-title{left:35px;top:657px;color:var(--heading-green);font-size:17px}
.projects-rule{left:35px;top:681px;width:310px;height:1px;background:linear-gradient(90deg,var(--heading-green),transparent)}
.thumb{width:154px;height:99px;border:2px solid var(--thumb-border)}
.pager{left:34px;top:908px;display:flex;gap:6px;font-size:13px;color:#333}
.pager span{width:20px;text-align:center;line-height:18px}
.pager .current{background:#ddd}
.divider{left:536px;top:440px;height:500px;border-left:1px dotted #c8c8c8}
.services-title{left:557px;top:436px;color:var(--heading-teal);font-size:18px}
.services-photo{left:555px;top:466px;width:225px;height:92px;border-radius:3px}
.services-text{left:557px;top:565px;width:222px;font-size:8.6px;line-height:13.5px}
.services-text u{color:#222}
.service-list{left:562px;top:644px;list-style:none;font-size:8.6px}
.service-list li{height:17px;display:flex;align-items:center;gap:5px}
.service-list a{color:var(--link-blue)}
.blog-title{left:559px;top:751px;color:var(--heading-teal);font-size:18px}
.blog-box{left:554px;top:785px;width:229px;height:132px;background:var(--blog-bg);padding:10px 14px}
.blog-box h3{font-weight:400;font-size:10px;color:var(--heading-teal);margin-bottom:4px}
.blog-box p{font-style:italic;font-size:8.4px;line-height:16.5px}
.view-all{left:559px;top:923px;font-size:10px;color:#555}
.footer{left:0;top:940px;width:822px;height:215px;background:linear-gradient(180deg,var(--footer-teal),var(--footer-deep))}
.footer h4{position:absolute;top:39px;font-weight:400;font-size:14px;color:#fff}
.footer-links{position:absolute;top:74px;list-style:none;font-size:9.5px;color:#fff}
.footer-links li{height:20px}
.footer-links li::before{content:"› ";}
.social{position:absolute;top:68px;left:368px;display:flex;gap:6px}
.social i{width:36px;height:36px;border-radius:50%;background:#fff;border:3px solid #d9eef5;display:block}
.news-text{position:absolute;left:556px;top:66px;width:225px;font-size:8.4px;line-height:12px;color:#fff}
.news-input{position:absolute;left:556px;top:104px;width:173px;height:19px;background:#fff;font-size:9px;color:#999;padding:3px 6px}
.news-btn{position:absolute;left:556px;top:132px;width:60px;height:17px;background:#1c6e8a;border-radius:2px;font-size:8.5px;color:#fff;text-align:center;line-height:17px}
.bottom-bar{left:0;top:1155px;width:822px;height:45px;background:var(--bar-light);font-size:11px;color:var(--bar-text);padding:13px 22px}
</style>
</head>
<body>
<div class="abs brand"><span class="brand-mark"></span><span class="brand-name">Lagoon Habitat</span></div>
<div class="abs search">type your word here
<svg width="16" height="16" viewBox="0 0 16 16"><circle cx="6" cy="6" r="4.5" fill="none" stroke="#8a9aa5" stroke-width="1.6"/><line x1="9.5" y1="9.5" x2="14" y2="14" stroke="#8a9aa5" stroke-width="2"/></svg></div>

<nav class="abs nav">
<a class="active" href="#"><span>Home</span></a><a href="#">About Us</a><a href="#">Services</a><a href="#">Gallery</a><a href="#">Projects</a><a href="#">Register</a><a href="#">Location</a><a href="#">Contact</a>
</nav>

<svg class="abs hero" viewBox="0 0 779 247" preserveAspectRatio="none">
<defs>
<linearGradient id="leafGlow" x1="0" y1="0" x2="1" y2="1"><stop offset="0" stop-color="#9fd07a"/><stop offset=".5" stop-color="#d8efb6"/><stop offset="1" stop-color="#6fb352"/></linearGradient>
<linearGradient id="birdTone" x1="0" y1="0" x2="1" y2="1"><stop offset="0" stop-color="#cfe9c8"/><stop offset=".5" stop-color="#3d7fd0"/><stop offset="1" stop-color="#a8d4a8"/></linearGradient>
</defs>
<g role="img" aria-label="Sunlit green leaves on a branch"><rect width="779" height="247" fill="url(#leafGlow)"/></g>
<g role="img" aria-label="Blue bird of paradise hanging from a branch"><polygon points="488,0 779,0 779,247 444,247" fill="url(#birdTone)"/></g>
<polygon points="484,0 488,0 444,247 440,247" fill="#fff"/>
</svg>
<div class="abs hero-caption">Encompassing Culture, Custom &amp; Science</div>
<div class="abs hero-dots"><i></i><i></i><i></i><i></i></div>

<main class="abs content"></main>

<h2 class="abs welcome-title">Welcome to Our Website Mainpage</h2>
<div class="abs welcome-text">
<p>Brightleaf Web Studio is a professional website design company dedicated to provide excellent services. We at Brightleaf Web Studio think graphic design as a combination and collaboration of ideas and technology. Our Website Design team give an unforgettable impression on the customers and the clients. We can assure you that this is the best place for requirement of yours regarding website design solutions</p>
<p>Brightleaf Web Studio provides you the Search Engine Optimization making your website search engine friendly. So that the website can achieve top position and ranking in the Internet searches and thereby increasing the scope for the website to be found by customers. We here modify the site to improve the ranking by using the keywords and contents.</p>
</div>
<div class="abs read-more">READ MORE <span style="color:#aaa">›</span></div>

<h2 class="abs projects-title">Our Projects</h2>
<div class="abs projects-rule"></div>
<div class="abs thumb" role="img" aria-label="Hummingbird in flight" style="left:34px;top:693px;background:linear-gradient(135deg,#b8501e,#6a7a3a,#c97c2a)"></div>
<div class="abs thumb" role="img" aria-label="Bluebird perched on a branch" style="left:193px;top:693px;background:linear-gradient(135deg,#5d7a2e,#2f62b8,#6b8a34)"></div>
<div class="abs thumb" role="img" aria-label="Colourful finch held in a hand" style="left:353px;top:693px;background:linear-gradient(135deg,#d8742a,#c9d83a,#8a6aa8)"></div>
<div class="abs thumb" role="img" aria-label="Indigo bunting on a perch" style="left:34px;top:798px;background:linear-gradient(135deg,#c9861e,#1e5fc2,#d59a2a)"></div>
<div class="abs thumb" role="img" aria-label="Lilac-breasted roller on a branch" style="left:193px;top:798px;background:linear-gradient(135deg,#6f8fc0,#a88ab8,#3d8aa0)"></div>
<div class="abs thumb" role="img" aria-label="Red cardinal on a green background" style="left:353px;top:798px;background:linear-gradient(135deg,#7a9a2a,#c8241e,#6a8a20)"></div>
<div class="abs pager"><span class="current">1</span><span>2</span><span>3</span><span>4</span></div>

<div class="abs divider"></div>

<h2 class="abs services-title">Some of Our Services</h2>
<div class="abs services-photo" role="img" aria-label="Hummingbird feeding at yellow flowers" style="background:linear-gradient(135deg,#3e9c7a,#7cc0a0,#c9c43a)"></div>
<p class="abs services-text"><u>So that the website can achieve top position and ranking in the Internet searches</u> and thereby increasing the scope for the website to be found by customers. We here modify the site to improve the ranking by using the keywords and contents.</p>
<ul class="abs service-list">
<li><svg width="10" height="8" viewBox="0 0 10 8"><path d="M1 1l4 3-4 3" fill="none" stroke="#4fa8d4" stroke-width="1.6"/></svg><a>Your Services puch line goes here</a></li>
<li><svg width="10" height="8" viewBox="0 0 10 8"><path d="M1 1l4 3-4 3" fill="none" stroke="#4fa8d4" stroke-width="1.6"/></svg><a>Services puch line goes here</a></li>
<li><svg width="10" height="8" viewBox="0 0 10 8"><path d="M1 1l4 3-4 3" fill="none" stroke="#4fa8d4" stroke-width="1.6"/></svg><a>Enviormental Service puch line goes here</a></li>
<li><svg width="10" height="8" viewBox="0 0 10 8"><path d="M1 1l4 3-4 3" fill="none" stroke="#4fa8d4" stroke-width="1.6"/></svg><a>Your Services puch line goes here</a></li>
<li><svg width="10" height="8" viewBox="0 0 10 8"><path d="M1 1l4 3-4 3" fill="none" stroke="#4fa8d4" stroke-width="1.6"/></svg><a>Services puch line goes here</a></li>
</ul>

<h2 class="abs blog-title">Recent Blog</h2>
<div class="abs blog-box">
<h3>YOUR FEED HEADLINE</h3>
<p>Brightleaf Web Studio is a web service company, offering a wide range of services which range from designing and development, that is covering almost all the fields in the best possible way. To be the best we know what and how to present beautifully</p>
</div>
<div class="abs view-all">VIEW ALL</div>

<footer class="abs footer">
<h4 style="left:30px">Usefull Links</h4>
<ul class="footer-links" style="left:30px"><li>Mainpage</li><li>About Our Company</li><li>Services Overview</li><li>Gallery</li></ul>
<ul class="footer-links" style="left:150px"><li>Feauted Gallery</li><li>Sitemap</li><li>News &amp; Blog</li><li>FAQ</li></ul>
<ul class="footer-links" style="left:256px"><li>News &amp; Artcies!</li><li>Feed Updates</li><li>Contact Us</li></ul>
<h4 style="left:367px">Get In Touch</h4>
<div class="social"><i></i><i></i><i></i></div>
<h4 style="left:556px">Newsletters Sign Up</h4>
<p class="news-text">Brightleaf Web Studio is a web service company, offering a wide range of services which range from designing</p>
<div class="news-input">yourr@emailaddres.com</div>
<div class="news-btn">Subscribe</div>
</footer>

<div class="abs bottom-bar">Copyright © 2012 Company Name. &nbsp;| &nbsp;All right reserved</div>
</body>
</html>
```